Business Card Design for company

We want new business cards. We'd like something different-- yet still highly professional. Our tagline is Providing leadership, delivering success. Stock photos are ok, as long as they are relevant and look upscale.

Target Market(s)

Architecture/Business Management Consulting/Engineering Consulting

Contact Information for Business Card

dark gray background with pops of blue might be good, but you tell me. You're the designers. Rounded corners might be nice, but again, you tell me.

Font styles to use
Serif
Sans Serif

Colors
3276b5
5c5c5c
9d9d9d
fbfbfb

Requirements
Nice to have
• Something different, but still very professional.

```html
<!DOCTYPE html>
<html lang="en">
<head>
<meta charset="utf-8">
<title>Varden Group – Business Card</title>
<link rel="stylesheet" href="https://fonts.googleapis.com/css2?family=Open+Sans:wght@400;600;700&display=swap">
<style>
  :root {
    --brand-blue: #3276b5;
    --mid-gray: #5c5c5c;
    --light-gray: #9d9d9d;
    --near-white: #fbfbfb;
    --card-black: #0f0f10;
    --backdrop: #3a3532;
  }
  * { box-sizing: border-box; margin: 0; padding: 0; }
  html, body {
    width: 1200px; height: 844px; overflow: hidden;
    background: var(--backdrop);
    font-family: "Open Sans", Arial, sans-serif;
  }
  .canvas {
    position: relative; width: 1200px; height: 844px;
    display: flex; align-items: center; justify-content: center; gap: 40px;
  }
  .card {
    position: relative; width: 540px; height: 310px;
    background: var(--card-black); border-radius: 12px; overflow: hidden;
  }

  /* Contact side */
  .card--contact { display: flex; }
  .brand-panel {
    width: 52%; display: flex; align-items: center; justify-content: center;
    border-right: 1px solid #2a2a2c;
  }
  .brand-name {
    color: var(--brand-blue); font-weight: 700; font-size: 30px;
    letter-spacing: 1px; text-transform: uppercase;
  }
  .contact-panel {
    width: 48%; padding: 62px 20px 0 26px; color: var(--near-white);
  }
  .person-name {
    color: var(--brand-blue); font-weight: 600; font-size: 17px;
    text-transform: uppercase; letter-spacing: .5px; line-height: 1.1;
  }
  .person-role { font-size: 13px; color: var(--near-white); margin-bottom: 6px; }
  .contact-list { list-style: none; font-size: 13px; line-height: 1.5; }
  .contact-list li { display: flex; align-items: center; gap: 8px; }
  .contact-list svg { width: 11px; height: 11px; fill: var(--brand-blue); flex: none; }
  .address { font-size: 13px; line-height: 1.45; margin-top: 8px; padding-left: 19px; }

  /* Brand side */
  .card--brand {
    display: flex; flex-direction: column; align-items: center; justify-content: center;
    gap: 60px;
  }
  .card--brand .brand-name { color: var(--near-white); font-size: 34px; letter-spacing: 2px; }
  .tagline {
    color: var(--near-white); font-size: 12px; font-weight: 600;
    letter-spacing: .6px; text-transform: uppercase;
  }
</style>
</head>
<body>
<main class="canvas">
  <section class="card card--contact">
    <div class="brand-panel">
      <span class="brand-name">Varden Group</span>
    </div>
    <div class="contact-panel">
      <h1 class="person-name">Daniel Morrow</h1>
      <p class="person-role">Managing Director</p>
      <ul class="contact-list">
        <li><svg viewBox="0 0 12 12" aria-hidden="true"><path d="M1 3c0-1 1-2 2-2h1l1 3-1.5 1a6 6 0 0 0 3.5 3.5L8 7l3 1v1c0 1-1 2-2 2A8 8 0 0 1 1 3z"/></svg>044-555 010 200</li>
        <li><svg viewBox="0 0 12 12" aria-hidden="true"><path d="M3.5 0h5a1 1 0 0 1 1 1v10a1 1 0 0 1-1 1h-5a1 1 0 0 1-1-1V1a1 1 0 0 1 1-1zm.5 1.5v7.5h4V1.5z"/></svg>044-555 010 300</li>
        <li><svg viewBox="0 0 12 12" aria-hidden="true"><path d="M0 2h12v8H0zm1 1v.3l5 3.2 5-3.2V3z"/></svg>info@vardengroup.com</li>
        <li><svg viewBox="0 0 12 12" aria-hidden="true"><circle cx="6" cy="6" r="5.5"/></svg>www.vardengroup.com</li>
      </ul>
      <p class="address">48 Harbour Lane, Suite 9<br>Northfield, 204816.</p>
    </div>
  </section>

  <section class="card card--brand">
    <span class="brand-name">Varden Group</span>
    <p class="tagline">Providing leadership, delivering success</p>
  </section>
</main>
</body>
</html>
```